Systems and Technology Consultants - Website

Design & Build a website for a new company which operates in the Systems and Technology space for Transportation, Government and Commercial sectors.

Overall design should be minimalist in nature.
Should also have a feed that provides news and event updates on the main page.
Logo has already been awarded and should be incorporated into the site.

We like the overall layout, functionality and simplicity of the below sites. Submitted designs could be similar to or a combination of the aspects on these sites, or perhaps a whole different concept - we are open to new ideas.
Norvique.com
Teblo.it

Update 1 Dated 27 May 2014

All I am moving away from the Teblo.it website and would like it to be more aligned with Norvique.com not only in layout but in functionality. I will be extending the deadline of this design brief for two weeks to incorporate additional requirements and will add addtional funding to the project.

Apologies for not having more information available to provide but with so many submissions its getting confusing.

Thanks Derek

Please note that the brief has been updated and the deadline has been extended.

Important: We will need two language versions of the website, English and Arabic; the website is hosted on HostPelican

Hello All, Thank you for your submissions. We have narrowed it down to the final 6 designers and I just wanted to take a moment and provide a bit of feedback regarding the concepts that we like and the modifications we are looking for. First, let me mention some of the design functions we like. - At the top of the homepage we really like the "region" or "language" tab so that the website can be viewed in both English and Arabic. - We like the homepage to have clear color variation so that the different sections of the homepage are distinct. Additionally, we like the bottom portion of the homepage to be in red. We feel that draws attention to our contact information. Again, we would like the colors to integrate black, gray-scale, red, etc. - Having a search tab at the top of the home page, or integrated into the main image, so that the site is easy to navigate. - We especially like the main image to have the scrolling tabs at the bottom so it is easy to browse the services offered (Consultancy, Solutions Architecture, Masters Systems Integration, Independent Design Review). - In regards to the services offered tab we really like the idea that a few people presented that have the outside of our logo with an icon in the middle of consultancy, solutions, etc., etc. Secondly, as mentioned in our brief we really enjoy the design of norvique site. Specially, we enjoy the strong iconic images they use, the way the tabs at the top scroll easily, and contact us page that generates an email. Lastly, I've included some photos of the concept we have been working on. What we are trying to demonstrate is how our company offers a range of services that are essentially linked together. We provide individual services that when combined present the full service package. We would like this concept to be integrated into the over concept of our website. Please feel free to ask for clarification of any of the above points or contact us if you have any additional questions. We appreciate all of your hard work and are very excited to see the updated designs. Best, Marta Vennick Quelbrant Senior Program Manager marta.vennick@quelbrant-example.com

Industry/Entity Type

Government

Font styles to use
Serif
Sans Serif

Requirements
Must have
• Must work on/adapt to various/mobile devices (responsive)
Must be simple and straightforward
Colors should be in line/matching with logo
2 language versions: English and Arabic (no Thai)
Services should be the first group/row of items after/below the main image
Note: the website will be hosted by hostpelican
Nice to have
• Submit feedback form
What's New section
The banner at the bottom of the site should not be too large; we would like a narrow one more
It would be nice if the header/top banner (with Home, About, etc. tabs) could stay in place as you scroll down (like Norvique and Chatterloop)
We will likely only use one image with a Company slogan on the Home page rather than a carousel of images to rotate through
Should not have
• This is the existing website: http://www.quelbrant-example.org
We do not like the animation, the way the banner icons/titles bounce
Not simple enough, we don't like the functionality or how pages load so slowly
We do not like the logo centered - it should be at the left
The banner and its tabs should not be towards the right, we would like them to be centered, to go all the way across and to be below the logo

```html
<!DOCTYPE html>
<html lang="en">
<head>
<meta charset="utf-8">
<title>Quelbrant — Systems and Technology Consultants</title>
<link href="https://fonts.googleapis.com/css2?family=Open+Sans:wght@400;600;700&display=swap" rel="stylesheet">
<style>
:root{
  --red:#d9241c;
  --dark:#1f1f21;
  --darker:#171718;
  --text:#555;
  --muted:#888;
  --light:#f2f2f2;
  --line:#e2e2e2;
  --white:#fff;
}
*{box-sizing:border-box;margin:0;padding:0}
html,body{width:667px;height:1200px;overflow:hidden;background:var(--white)}
body{font-family:"Open Sans",Arial,sans-serif;color:var(--text);font-size:6.5px;line-height:1.5}
.wrap{width:560px;margin:0 auto;position:relative}
a{color:inherit;text-decoration:none}

.topbar{height:14px;background:var(--darker);color:#ccc;font-size:6px}
.topbar .wrap{display:flex;gap:14px;align-items:center;height:14px}
.topbar span{display:flex;align-items:center;gap:4px}
.topbar i{display:inline-block;width:7px;height:7px;background:var(--red)}

.header{height:30px;border-bottom:1px solid var(--line)}
.header .wrap{display:flex;justify-content:space-between;align-items:center;height:30px}
.brand{display:flex;align-items:center;gap:6px;font-weight:700;font-size:11px;color:var(--dark);letter-spacing:1px}
.brand b{width:14px;height:14px;background:var(--dark)}
.nav{display:flex;gap:16px;font-size:6.5px;color:#444}
.nav a{padding:10px 0}
.nav .active{color:var(--red);border-bottom:2px solid var(--red);font-weight:600}

.hero{height:246px;position:relative;background:linear-gradient(115deg,#dfe6ee 0%,#9fb0c4 35%,#4b6682 70%,#1e3350 100%)}
.hero-copy{position:absolute;left:53px;top:125px;font-size:12px;line-height:1.25;color:var(--dark)}
.hero-copy span{display:inline-block;background:rgba(255,255,255,.92);padding:2px 6px;margin-bottom:3px}
.hero-copy em{font-style:normal;background:var(--red);color:var(--white);padding:0 3px;margin-left:-6px;display:inline-block;padding:2px 5px;font-weight:600}

.services{height:230px;padding-top:44px}
.services .wrap{display:grid;grid-template-columns:repeat(3,1fr);gap:34px 30px}
.service h3{display:flex;align-items:center;gap:6px;font-size:8.5px;color:var(--dark);font-weight:600;margin-bottom:5px}
.service h3 i{width:14px;height:14px;background:var(--red);border-radius:2px;display:flex;align-items:center;justify-content:center}
.service p{padding-left:20px;color:var(--muted)}

.articles{height:280px;background:var(--light);padding-top:22px;border-top:1px solid var(--line)}
.section-title{font-size:10px;color:var(--dark);font-weight:600;padding-bottom:6px;border-bottom:1px solid var(--line);margin-bottom:12px}
.cards{display:grid;grid-template-columns:repeat(3,1fr);gap:20px}
.card .photo{height:88px;position:relative}
.card .photo .cap{position:absolute;left:0;right:0;bottom:0;background:rgba(20,20,20,.8);color:var(--white);font-size:7px;padding:4px 8px}
.card p{margin:9px 0 4px;color:var(--muted)}
.more{color:var(--red);font-weight:600;font-size:6px}

.news-about{height:215px;padding-top:20px}
.news-about .wrap{display:grid;grid-template-columns:230px 1fr;gap:30px}
.news-item{display:flex;gap:10px;margin-bottom:8px}
.date{width:22px;text-align:center;color:var(--red);font-size:12px;font-weight:700;line-height:1}
.date small{display:block;font-size:5.5px;color:var(--muted);font-weight:400;margin-top:2px}
.news-item h4{font-size:6.5px;color:var(--dark);font-weight:600}
.news-item p{color:var(--muted)}
.about-box{background:var(--light);padding:10px}
.about-top{display:flex;gap:10px;margin-bottom:6px}
.about-top .photo{width:90px;height:62px;flex:none}
.about-top h4{font-size:7.5px;color:var(--dark);font-weight:600;margin-bottom:3px}
.about-box p{color:var(--muted)}

.footer{height:170px;background:var(--dark);color:#aaa;padding-top:20px}
.footer .wrap{display:grid;grid-template-columns:90px 120px 90px 1fr;gap:16px}
.footer h5{color:var(--white);font-size:7px;font-weight:600;margin-bottom:6px}
.footer li{list-style:none;font-size:6px}
.socials{display:flex;gap:5px;margin-bottom:12px}
.socials i{width:14px;height:14px;background:#3a5a98}
.socials i:nth-child(2){background:#2aa3de}
.socials i:nth-child(3){background:#1a78b0}
.subscribe{display:flex}
.subscribe span{flex:1;height:13px;background:#2c2c2e;border:1px solid #3b3b3d}
.subscribe b{background:var(--red);color:var(--white);font-size:6px;padding:0 8px;line-height:13px;font-weight:600}
.bottombar{height:15px;background:var(--darker);color:#888;font-size:5.5px}
.bottombar .wrap{display:flex;justify-content:space-between;align-items:center;height:15px}
</style>
</head>
<body>
<div class="topbar"><div class="wrap"><span><i></i>0800-555-0142</span><span><i></i>info@quelbrant-example.com</span></div></div>

<header class="header"><div class="wrap">
  <div class="brand"><b></b>QUELBRANT</div>
  <nav class="nav"><a class="active">HOME</a><a>Business Units</a><a>Services</a><a>About Us</a><a>Locations</a><a>Contact Us</a></nav>
</div></header>

<section class="hero" role="img" aria-label="Hand touching a glowing digital interface with world map and network graphics">
  <div class="hero-copy">
    <span><em>Quelbrant specializes</em> in delivering quality</span><br>
    <span>professional services and technical</span><br>
    <span>projects that support larger business goals.</span>
  </div>
</section>

<section class="services"><div class="wrap">
  <div class="service"><h3><i></i>Consulting</h3><p>It is a long established fact that a reader will be distracted by the readable content of a page when looking at its layout.</p></div>
  <div class="service"><h3><i></i>Engineering</h3><p>It is a long established fact that a reader will be distracted by the readable content of a page when looking at its layout.</p></div>
  <div class="service"><h3><i></i>Construction</h3><p>It is a long established fact that a reader will be distracted by the readable content of a page when looking at its layout.</p></div>
  <div class="service"><h3><i></i>Operations</h3><p>It is a long established fact that a reader will be distracted by the readable content of a page when looking at its layout.</p></div>
  <div class="service"><h3><i></i>Maintenance</h3><p>It is a long established fact that a reader will be distracted by the readable content of a page when looking at its layout.</p></div>
  <div class="service"><h3><i></i>Our Vision</h3><p>It is a long established fact that a reader will be distracted by the readable content of a page when looking at its layout.</p></div>
</div></section>

<section class="articles"><div class="wrap">
  <h2 class="section-title">Our Articles</h2>
  <div class="cards">
    <article class="card"><div class="photo" role="img" aria-label="Business team meeting around a table" style="background:linear-gradient(135deg,#c9c4bd,#6d6660)"><div class="cap">Lorem Ipsum</div></div>
      <p>Fusce mauris dapibus, tellus cursus ac commodo, tortor condimentum nibh, ut fermentum massa justo sit amet. Vivamus sagittis lacus.</p><a class="more">Read More</a></article>
    <article class="card"><div class="photo" role="img" aria-label="Pen resting on technical drawings and charts" style="background:linear-gradient(135deg,#f0f0ee,#a9b2bb)"><div class="cap">Lorem Ipsum</div></div>
      <p>Fusce mauris dapibus, tellus cursus ac commodo, tortor condimentum nibh, ut fermentum massa justo sit amet. Vivamus sagittis lacus.</p><a class="more">Read More</a></article>
    <article class="card"><div class="photo" role="img" aria-label="Businessman standing under a stormy sky" style="background:linear-gradient(180deg,#3e4650,#9aa1a8)"><div class="cap">Lorem Ipsum</div></div>
      <p>Fusce mauris dapibus, tellus cursus ac commodo, tortor condimentum nibh, ut fermentum massa justo sit amet. Vivamus sagittis lacus.</p><a class="more">Read More</a></article>
  </div>
</div></section>

<section class="news-about"><div class="wrap">
  <div class="news">
    <h2 class="section-title">Our News</h2>
    <div class="news-item"><div class="date">27<small>FEB</small></div><div><h4>Lorem Ipsum is a simply text</h4><p>It is a long established fact that a reader will be distracted by the readable content.</p></div></div>
    <div class="news-item"><div class="date">30<small>FEB</small></div><div><h4>Lorem Ipsum is a simply text</h4><p>It is a long established fact that a reader will be distracted by the readable content.</p></div></div>
    <div class="news-item"><div class="date">30<small>FEB</small></div><div><h4>Lorem Ipsum is a simply text</h4><p>It is a long established fact that a reader will be distracted by the readable content.</p></div></div>
  </div>
  <div class="about">
    <h2 class="section-title">About Us</h2>
    <div class="about-box">
      <div class="about-top"><div class="photo" role="img" aria-label="Business growth chart with blue bars" style="background:linear-gradient(135deg,#e8eef4,#3f6fa0)"></div>
        <div><h4>Lorem Ipsum</h4><p>It is a long established fact that a reader will be distracted by the readable content of a page when looking at its layout. It is a long established fact that a reader will be distracted.</p></div></div>
      <p>It is a long established fact that a reader will be distracted by the readable content of a page when looking at its layout. It is a long established fact that a reader will be distracted by the readable content of a page when looking at its layout.</p>
      <a class="more">Read More</a>
    </div>
  </div>
</div></section>

<footer class="footer"><div class="wrap">
  <div><h5>Contact Info</h5><ul><li>12 Harbour Lane</li><li>Suite 400, Tower B</li><li>P.O. Box 2281</li><li>Tel: 0800-555-0142</li><li>info@quelbrant-example.com</li><li>Phone: 0800-555-0199</li></ul></div>
  <div><h5>About Us</h5><ul><li>Quelbrant delivers systems and technology consulting for transportation, government and commercial clients, linking each service into one complete and dependable package.</li></ul></div>
  <div><h5>Company Info</h5><ul><li>Home</li><li>Business Units</li><li>Services</li><li>About Us</li><li>Locations</li><li>Contact Us</li></ul></div>
  <div><h5>Stay updates on our Social Network</h5><div class="socials"><i></i><i></i><i></i></div>
    <h5>Join Our Newsletter</h5><div class="subscribe"><span></span><b>Subscribe</b></div></div>
</div></footer>
<div class="bottombar"><div class="wrap"><span>© Copyright 2014 Quelbrant. All Rights Reserved</span><span>Privacy Policy | Terms of Use</span></div></div>
</body>
</html>
```